AI Business Tools Landing Page

My web-based website builder (Pavlora.com) will be adding many new features in the very near future and I need an eye-catching landing page to promote these new products.

The page will have a primary section of the 8 main products we are promoting:
1. AI Instant Website Generator
2. AI Chatbot
3. Online Store Builder with AI Assistance
4. AI Auto-Blogging System
5. Online Scheduling System
6. Custom Email System
7. SEO Service
8. CRM System

The page will also have a smaller section for links to our affiliate programs. These can be smaller, less-promanent buttons or links. These are the affiliate products:
1. Get Your LLC
2. Website Design and Maintenance
3. Google Ads Management
4. Social Media Posting Service
5. Logo Design
6. Trademark Registration
7. Patent Application
8. Printing Services (including postcards, flyers, and merch.)
9. Bulk AI Content Generator

The theme and color scheme of the page should follow the theme of our main website, which is https://pavlora.com.

I need the page fully coded and ready to deploy on my server.

I look forward to seeing your amazing designs!

```html
<!DOCTYPE html>
<html lang="en">
<head>
<meta charset="UTF-8">
<title>Pavlora – AI Business Tools</title>
<link href="https://fonts.googleapis.com/css2?family=Poppins:ital,wght@0,400;0,500;0,600;0,700;1,600;1,700&family=Open+Sans:wght@400;600&display=swap" rel="stylesheet">
<style>
  :root {
    --page-bg: #ffffff;
    --ink: #111418;
    --accent-blue: #5ec8f6;
    --nav-bg: #1d3a56;
    --hero-dark: #05171b;
    --hero-teal: #0f4a4a;
    --cta-green: #7ee0a2;
    --white: #ffffff;
    --soft-bg: #eff3f8;
  }
  * { box-sizing: border-box; margin: 0; padding: 0; }
  html, body {
    width: 1200px; height: 1200px; overflow: hidden;
    background: var(--page-bg);
    font-family: "Poppins", sans-serif;
    color: var(--ink);
  }
  .page { position: relative; width: 1200px; height: 1200px; }
  .column { position: absolute; left: 137px; width: 926px; }

  .top-strip {
    top: 0; height: 80px;
    background: linear-gradient(90deg, #04161a, #0c3434 40%, #07201f 70%, #04161a);
  }

  .section-label {
    font-style: italic; font-weight: 600; font-size: 15px;
    color: var(--accent-blue); text-align: center;
  }
  .section-title {
    font-weight: 600; font-size: 27px; line-height: 38px;
    text-align: center;
  }
  .features-head { top: 120px; }
  .features-head .section-title { margin-top: 12px; }

  .hero {
    top: 271px; height: 658px;
    border-radius: 18px; overflow: hidden;
    background: var(--hero-dark);
  }
  .nav {
    height: 74px; background: var(--nav-bg);
    display: flex; align-items: center; padding: 0 27px;
  }
  .brand { display: flex; align-items: center; gap: 12px; color: var(--white); font-weight: 500; font-size: 25px; }
  .brand-mark { width: 34px; height: 34px; background: var(--accent-blue); }
  .nav-links { margin-left: auto; display: flex; align-items: center; gap: 16px; font-size: 11px; color: var(--white); }
  .btn-login { border: 1.5px solid var(--white); border-radius: 3px; padding: 4px 12px; font-weight: 500; }
  .btn-start { background: var(--cta-green); border-radius: 3px; padding: 6px 10px; font-weight: 600; font-size: 10px; }

  .hero-visual {
    position: absolute; top: 74px; left: 0; right: 0; bottom: 0;
    background: radial-gradient(ellipse at 50% 48%, #1b5856 0%, var(--hero-teal) 25%, #082628 55%, var(--hero-dark) 100%);
  }
  .hero-copy {
    position: absolute; top: 318px; left: 0; right: 0;
    text-align: center; color: var(--white);
  }
  .hero-title { font-weight: 600; font-size: 41px; line-height: 48px; }
  .hero-title em { font-style: italic; font-weight: 700; color: var(--accent-blue); }
  .hero-sub { margin-top: 16px; font-family: "Open Sans", sans-serif; font-size: 13.5px; line-height: 18px; }
  .hero-btn {
    display: inline-block; margin-top: 22px; width: 268px; height: 38px; line-height: 38px;
    border-radius: 19px; background: var(--accent-blue);
    font-size: 12px; font-weight: 600; color: var(--white);
  }

  .why {
    top: 975px; height: 225px;
    background: var(--soft-bg);
    border-radius: 18px 18px 0 0;
    padding-top: 50px;
  }
  .why .section-title { margin-top: 8px; }
  .why-banner {
    position: absolute; left: 26px; right: 26px; top: 206px; height: 40px;
    border-radius: 4px;
    background: linear-gradient(90deg, #8a1030, #3a1a5e 45%, #1a3a8a 75%, #0b1a3c);
  }
</style>
</head>
<body>
<div class="page">
  <div class="column top-strip" role="img" aria-label="Dark teal circuit board background"></div>

  <header class="column features-head">
    <p class="section-label">Features</p>
    <h2 class="section-title">AI Tools to Power Every Aspect of<br>Your Business</h2>
  </header>

  <section class="column hero">
    <nav class="nav">
      <div class="brand"><span class="brand-mark"></span>Pavlora</div>
      <div class="nav-links">
        <span>Home</span><span>Features</span><span>Pricing</span><span>Testimonials</span><span>Contact</span>
        <span class="btn-login">Log in</span>
        <span class="btn-start">Get Started for FREE!</span>
      </div>
    </nav>
    <div class="hero-visual" role="img" aria-label="Glowing circuit board with large AI letters in a chip outline"></div>
    <div class="hero-copy">
      <h1 class="hero-title">Revolutionize Your<br>Website Creation with <em>AI</em></h1>
      <p class="hero-sub">Effortlessly build, manage, and scale your online presence with cutting-edge AI<br>tools. Launch your website in minutes, no coding required.</p>
      <span class="hero-btn">Build my free website</span>
    </div>
  </section>

  <section class="column why">
    <p class="section-label">Why Choose Pavlora</p>
    <h2 class="section-title">Why Choose Pavlora for Your<br>AI Business Tools?</h2>
    <div class="why-banner" role="img" aria-label="Colourful red to blue banner image"></div>
  </section>
</div>
</body>
</html>
```